OWNERS HANDBOOK

Take a MICROSOFT WORD document and turn it into a nicely designed and structured PDF or similar to circulate to Owners and to make available online for Owners to access.

```html
<!DOCTYPE html>
<html lang="en">
<head>
<meta charset="utf-8">
<title>Owners Handbook 2023 – Page Spread</title>
<link href="https://fonts.googleapis.com/css2?family=Poppins:wght@500;600;700&family=Arimo:wght@400;700&display=swap" rel="stylesheet">
<style>
:root{
  --blue:#1565c0;
  --navy:#0d3f7a;
  --bright:#1e88e5;
  --grey-tag:#c7c9ce;
  --paper:#f6f7f9;
  --ink:#2b2b2b;
  --red:#d32f2f;
  --backdrop:#cfd0d2;
}
*{box-sizing:border-box;margin:0;padding:0}
html,body{width:890px;height:1200px;overflow:hidden;background:var(--backdrop)}
body{position:relative;font-family:Arimo,Arial,sans-serif;color:var(--ink)}
.page{position:absolute;width:192px;height:273px;overflow:hidden;
  background:linear-gradient(135deg,#ffffff 0%,var(--paper) 50%,#eef0f3 100%);
  box-shadow:0 1px 4px rgba(0,0,0,.25)}
.page::after{content:"";position:absolute;left:0;right:0;bottom:0;height:12px;
  background:linear-gradient(90deg,var(--navy),var(--bright))}
.c1{left:43px}.c2{left:248px}.c3{left:453px}.c4{left:658px}
.r1{top:30px}.r2{top:318px}.r3{top:606px}.r4{top:893px}
.pad{padding:14px 9px 0}
p,li{font-size:4.3px;line-height:1.32;text-align:justify}
p{margin-bottom:4.2px}
.sec{display:inline-block;white-space:nowrap;font-family:Poppins,sans-serif;font-weight:600;color:var(--navy);
  font-size:7px;background:var(--grey-tag);padding:3px 6px;border:1px solid var(--bright);
  box-shadow:1.5px 1.5px 0 #fff,2.5px 2.5px 0 var(--bright);margin-bottom:7px}
.sec.wide{display:block;white-space:normal}
.sec.sm{font-size:6px}
.lead{color:var(--blue)}
.item{display:flex;gap:4px;margin-bottom:4.6px}
.item .n{flex:0 0 8px;color:var(--blue);font-family:Poppins,sans-serif;font-weight:700;font-size:5px;line-height:1.1}
.item p{margin:0}
h3{font-family:Poppins,sans-serif;color:var(--navy);font-size:6px;font-weight:700;margin:3px 0 3px}
/* cover */
.cover .year{position:absolute;left:0;right:0;top:12px;text-align:center;font-family:Poppins,sans-serif;
  font-weight:700;font-size:33px;color:var(--blue);line-height:1}
.cover .year::before,.cover .year::after{content:"";position:absolute;top:15px;width:30px;height:2px;background:var(--bright)}
.cover .year::before{left:24px}.cover .year::after{right:24px}
.cover .sub{position:absolute;top:47px;left:0;right:0;text-align:center;font-family:Poppins,sans-serif;
  font-weight:600;font-size:9px;color:var(--blue)}
.cover .rule{position:absolute;left:11px;right:0;height:1.5px;background:var(--bright)}
.cover .photo{position:absolute;left:0;right:0;top:75px;height:151px;
  background:linear-gradient(180deg,#9aa4a6 0%,#c0826a 30%,#5f7d52 60%,#7d9a63 100%)}
.cover .title{position:absolute;left:17px;right:0;top:114px;height:72px;background:rgba(16,72,58,.88);
  display:flex;align-items:center;justify-content:center;text-align:center;color:#fff;
  font-family:Poppins,sans-serif;font-weight:600;font-size:13px;line-height:1.45}
.cover .addr{position:absolute;left:24px;top:245px;display:flex;gap:6px;align-items:center;
  font-family:Poppins,sans-serif;font-weight:600;font-size:7.6px;color:var(--blue);line-height:1.4}
.cover::after{display:none}
.doc-title{font-family:Poppins,sans-serif;font-weight:600;color:var(--navy);font-size:9px;text-align:center;margin:1px 0 12px}
.notice{font-size:4.2px;line-height:1.3;margin-bottom:24px}
table.contacts{width:168px;margin-left:3px;border-collapse:collapse;border:0.6px solid #9bb;font-size:2.5px}
table.contacts td{padding:0.9px 2px;border-bottom:0.4px solid #ccd;line-height:1}
table.contacts td:first-child{width:60%;font-weight:700;border-right:0.4px solid #ccd}
table.contacts td:last-child{text-align:center;font-size:3px}
table.contacts .red td{color:var(--red)}
table.contacts .bar td{background:#2b8fd8;height:5px}
.toc h2{font-family:Poppins,sans-serif;font-weight:600;color:var(--navy);font-size:9px;text-align:center;margin-bottom:6px}
.toc li{list-style:none;font-size:4.8px;line-height:1.2;color:var(--blue);border-bottom:0.4px solid #d4d8de;padding:1px 0;margin-bottom:2.4px;text-align:left;white-space:nowrap}
.board{width:100%;border-collapse:collapse;margin:4px 0 10px}
.board td{font-size:4.2px;padding:2.6px 0;white-space:nowrap}
.board td:first-child{width:42px}
.ico{display:inline-block;vertical-align:middle;margin-right:2px}
.callout{border:0.8px solid var(--blue);padding:4px;font-weight:700;font-size:4.2px;line-height:1.32;color:var(--navy);margin-top:8px}
.group{font-family:Poppins,sans-serif;font-weight:600;color:var(--blue);font-size:6.4px;margin-top:4px;padding-left:6px}
.svc{display:flex;align-items:center;gap:4px;font-size:4.3px;margin-bottom:3.6px}
.mand{color:var(--blue);font-weight:700;font-size:4.6px;margin-bottom:5px}
.mand b{font-family:Poppins,sans-serif;font-size:7px}
.forbid{font-family:Poppins,sans-serif;font-weight:700;color:var(--blue);font-size:6.4px;margin:6px 0 5px}
.important{display:flex;align-items:center;gap:7px;margin:28px 0 20px}
.important span{font-family:Poppins,sans-serif;font-weight:600;color:var(--red);font-size:6.6px}
.tick{display:flex;gap:5px;margin-bottom:5px}
.tick p{margin:0}
.biz{display:flex;align-items:center;font-size:4.3px;margin-bottom:3.5px}
.biz .name{flex:0 0 62px;display:flex;align-items:center;gap:4px}
.biz .tel{display:flex;align-items:center;gap:3px}
.hint{font-size:4.3px;margin:-1px 0 8px;white-space:nowrap;overflow:hidden}
</style>
</head>
<body>

<section class="page cover c1 r1">
  <div class="year">2023</div>
  <div class="sub">OWNERS HANDBOOK</div>
  <div class="rule" style="top:69px"></div>
  <div class="photo" role="img" aria-label="Aerial photograph of the resort: terracotta-roofed apartment blocks around green gardens and swimming pools"></div>
  <div class="title">MONTE AZUL VILLAGE<br>AND<br>VILLAGE GARDENS</div>
  <div class="rule" style="top:230px"></div>
  <div class="addr">
    <svg width="16" height="18" viewBox="0 0 16 18"><path d="M8 0a6 6 0 0 0-6 6c0 4.5 6 10 6 10s6-5.5 6-10a6 6 0 0 0-6-6z" fill="var(--bright)"/><circle cx="8" cy="6" r="2.4" fill="#fff"/><ellipse cx="8" cy="16.5" rx="6" ry="1.3" fill="none" stroke="var(--bright)" stroke-width="1"/></svg>
    <div>Monte Azul Resort, 8000 - 123,<br>Vale do Sol, Portugal</div>
  </div>
</section>

<section class="page c2 r1"><div class="pad">
  <div class="sec" style="width:72px">Preface</div>
  <div class="doc-title">— Owners Handbook - 2023 —</div>
  <p>This handbook has been constructed and produced for the benefit of the Monte Azul Owners and has been produced by existing Monte Azul Owners who have volunteered their time and efforts in the Handbook's production.</p>
  <p>If anything of note is missing or incorrect, then please let a Board member know and this will ensure the next version is improved.</p>
</div></section>

<section class="page c3 r1"><div class="pad">
  <div class="sec" style="width:82px">Useful Contacts</div>
  <p class="notice">PLEASE NOTE THE SUFFIX CODE FOR ALL APART FROM THE EMERGENCY SERVICES IF NOT USING A PORTUGUESE MOBILE IS 00351 or +351</p>
  <table class="contacts">
    <tr><td>POLICE – EMERGENCY</td><td>112</td></tr>
    <tr><td>FIRE BRIGADE</td><td>112</td></tr>
    <tr><td>AMBULANCE</td><td>112</td></tr>
    <tr class="red"><td>EMERGENCY DOCTOR</td><td>CALL SECURITY</td></tr>
    <tr class="bar"><td></td><td></td></tr>
    <tr><td>RESORT CUSTOMER SERVICE</td><td>289 000 101</td></tr>
    <tr><td>RESORT CUSTOMER SERVICE</td><td>289 000 102</td></tr>
    <tr><td>CONDOMINIUM OFFICE (OUT OF HOURS)</td><td>960 000 103</td></tr>
    <tr class="red"><td>SECURITY OFFICE</td><td>289 000 104</td></tr>
    <tr class="red"><td>SECURITY MOBILE</td><td>920 000 105</td></tr>
    <tr><td>LOCAL POLICE (TOWN)</td><td>289 000 106</td></tr>
    <tr><td>LOCAL POLICE (MARINA)</td><td>289 000 107</td></tr>
    <tr><td>MEDICAL CENTRE</td><td>289 000 108</td></tr>
    <tr><td>CLINIC – TOWN CENTRE</td><td>289 000 109</td></tr>
    <tr><td>PHARMACY – HIGH STREET</td><td>289 000 110</td></tr>
    <tr><td>PHARMACY – OLD TOWN</td><td>289 000 111</td></tr>
    <tr><td>PHARMACY – MARKET</td><td>960 000 112</td></tr>
    <tr><td>HOSPITAL (CITY)</td><td>289 000 113</td></tr>
    <tr class="red"><td>HOSPITAL – NEAREST ONE</td><td>289 000 114</td></tr>
    <tr><td>ELECTRICITY 24H ASSISTANCE</td><td>800 000 115</td></tr>
    <tr><td>GAS 24H ASSISTANCE</td><td>800 000 116</td></tr>
    <tr><td>GAS SUPPLIER 24H</td><td>210 000 117</td></tr>
    <tr><td>WATER 24H ASSISTANCE</td><td>289 000 118</td></tr>
    <tr class="red"><td>TAXIS AND LIMO SERVICE</td><td>960 000 119 / 960 000 120</td></tr>
    <tr class="red"><td>OTHER TAXIS</td><td>289 000 121 / 289 000 122</td></tr>
    <tr><td>AIRPORT</td><td>289 000 123</td></tr>
    <tr><td>BUS STATION</td><td>289 000 124</td></tr>
    <tr><td>TRAIN STATION</td><td>289 000 125</td></tr>
    <tr><td>LOCKSMITH – TOWN</td><td>960 000 126</td></tr>
  </table>
</div></section>

<section class="page toc c4 r1"><div class="pad" style="padding-top:8px">
  <h2>Table of Contents</h2>
  <ul>
    <li>Preface</li><li>Useful Contacts</li><li>Monte Azul Village and Village Gardens - Introduction</li>
    <li>Our Board</li><li>Owners - Primary Obligations</li><li>Valuable Information</li>
    <li>Your Apartmen</li><li>Our Rules and Regulations</li><li>The Gardens Common Area – CLUB RULES</li>
    <li>TV and Internet Services</li><li>Local Knowledge</li><li>Restaurants – Cafes – Shops</li>
    <li>Communal WIFI 15</li><li>Waste Disposal15</li><li>Cash Machines (ATM) 15</li>
    <li>Electricity Supply 15</li><li>Apartment Alarms</li><li>Pool and Gardens Maintenance</li>
    <li>Fire Safety</li><li>Public Transport 16</li><li>Appendix 1 – PEAK SEASON PROCEDURE</li>
    <li>Appendix 2 – FIRE EVACUATION PROCEDURES</li>
  </ul>
</div></section>

<section class="page c1 r2"><div class="pad">
  <div class="sec wide" style="font-size:6.6px">Monte Azul Village and Village Gardens - Introduction</div>
  <p>The primary purpose of this Owners Handbook is to provide the Owners with valuable up to date information on all things Monte Azul Village and Gardens.</p>
  <p>The Monte Azul Village (MAV) development represents a five-phase property development of 194 apartments comprising a combination of two and three-bedroom units.</p>
  <p>As Owners, we have made financial investments for our respective property at Monte Azul and as Owners we also have Obligations to ensure we all support the investments made by ensuring our property assets are not only protected but retain and enhance in value through the years.</p>
  <p>Monte Azul Village (MAV) and Monte Azul Gardens (MAG) are quite unique compared to other condominium properties in the Algarve and as such our uniqueness adds value to our investment. It's in all our interests to ensure we contribute to the continuing value enhancement of Monte Azul Village and Gardens by contributing to our future successes.</p>
  <p>Throughout the years since the Condominium has existed, Owners have been the foundation of our success and without naming any individual Owners, many have contributed directly by taking responsibility for being on the "Monte Azul Village and Gardens - Owners Board" and in doing so they have given immense value to our overall resort well-being and success.</p>
  <p>Board members provide many hours on behalf of all the Owners, for zero remuneration and as such they should be commended for their selfless commitments.</p>
  <div class="callout">We do have a legal structure including Rules and Regulations for all aspects of the Condominium and these can be found in the separate "Monte Azul Owners – Rules and Regulations" publication.</div>
</div></section>

<section class="page c2 r2"><div class="pad">
  <div class="sec" style="width:82px">Our Board</div>
  <p>Annually at the Owners General Meeting (held typically in Q1 of each year), Owners have the opportunity of being nominated and thereafter selected by the Owners voting for them to become an active member of the Owners Board.</p>
  <p>Our selected Board Members have in recent years agreed voluntarily to perform their respective roles on the board for a 12-month term, without receiving any remuneration. A magnanimous commitment considering the hours that each Board Members allocates to the successful management and operation of the Complex, on the Owners behalf.</p>
  <p class="lead">Current (2022 – 2023) Board Members and respective contact details are as follows:</p>
  <table class="board">
    <tr><td>Paul Hartley</td><td><svg class="ico" width="6" height="4.5" viewBox="0 0 6 4.5"><rect width="6" height="4.5" fill="var(--navy)"/><path d="M0 0l3 2.4L6 0" stroke="#fff" stroke-width=".6" fill="none"/></svg>p.hartley@example.net</td><td><svg class="ico" width="4" height="5" viewBox="0 0 4 5"><path d="M1 0h1v1.4H1.3c-.1 1 .2 1.6.8 2.2H3V5H2C.5 4 0 2.6 0 1.4 0 .6.4 0 1 0z" fill="var(--navy)"/></svg>+44 7700 900123</td></tr>
    <tr><td>Diane Morrow</td><td><svg class="ico" width="6" height="4.5" viewBox="0 0 6 4.5"><rect width="6" height="4.5" fill="var(--navy)"/><path d="M0 0l3 2.4L6 0" stroke="#fff" stroke-width=".6" fill="none"/></svg>d.morrow@example.com</td><td><svg class="ico" width="4" height="5" viewBox="0 0 4 5"><path d="M1 0h1v1.4H1.3c-.1 1 .2 1.6.8 2.2H3V5H2C.5 4 0 2.6 0 1.4 0 .6.4 0 1 0z" fill="var(--navy)"/></svg>+44 7700 900456</td></tr>
    <tr><td>Claire Dubois</td><td><svg class="ico" width="6" height="4.5" viewBox="0 0 6 4.5"><rect width="6" height="4.5" fill="var(--navy)"/><path d="M0 0l3 2.4L6 0" stroke="#fff" stroke-width=".6" fill="none"/></svg>c.dubois@example.org</td><td><svg class="ico" width="4" height="5" viewBox="0 0 4 5"><path d="M1 0h1v1.4H1.3c-.1 1 .2 1.6.8 2.2H3V5H2C.5 4 0 2.6 0 1.4 0 .6.4 0 1 0z" fill="var(--navy)"/></svg>+32 470 00 0789</td></tr>
    <tr><td>Sean Brady</td><td><svg class="ico" width="6" height="4.5" viewBox="0 0 6 4.5"><rect width="6" height="4.5" fill="var(--navy)"/><path d="M0 0l3 2.4L6 0" stroke="#fff" stroke-width=".6" fill="none"/></svg>s.brady@example.net</td><td><svg class="ico" width="4" height="5" viewBox="0 0 4 5"><path d="M1 0h1v1.4H1.3c-.1 1 .2 1.6.8 2.2H3V5H2C.5 4 0 2.6 0 1.4 0 .6.4 0 1 0z" fill="var(--navy)"/></svg>+44 7700 900987</td></tr>
  </table>
  <div class="sec" style="margin-bottom:4px">Owner Communication</div>
  <h3 style="font-size:7px">FRIENDHUB GROUP</h3>
  <p>Although all legal communications are originated by the Condominium Administrator, CDC, the Board has created an exclusive (informal) communication forum for Owners, through using a FriendHub group, named: Although all legal communications are originated by the Condominium Administrator, CDC, the Board has created an exclusive (informal) communication forum for Owners, through using a FriendHub group, named:</p>
  <div class="group">•Monte Azul OwnersGroup</div>
</div></section>

<section class="page c3 r2"><div class="pad">
  <div class="sec" style="font-size:7.2px;padding:5px 8px;margin-bottom:10px">Property Management Company</div>
  <p>It is the responsibility of the Board of Directors to appoint a suitably experienced and cost-effective Property Management Company to provide a comprehensive range of services to ensure the smooth running of the condominium (and in our case our Central Area also), including all aspects of gardening, swimming pools management, security, TV services, Internet services, upkeep of the buildings and so much more.</p>
  <p>The current incumbent Property Management Company is Casa do Condomínio (CDC) who have an office in Praia Nova, and whose contact details are listed earlier within this Handbook.</p>
  <p class="lead" style="margin-top:8px">Property Maintenance is a key component of the Property Management services that CDC provides, and as such they are in most instances the first point of contact should an Owner require assistance on matters relating to:</p>
  <div class="svc"><svg width="8" height="7" viewBox="0 0 8 7"><path d="M4 0L0 3h1v4h6V3h1z" fill="var(--navy)"/></svg>External aspects of each apartment (roofing, handrails</div>
  <div class="svc" style="padding-left:12px">/ external tiles, stairwells, elevators etc.)</div>
  <div class="svc"><svg width="8" height="7" viewBox="0 0 8 7"><path d="M1 7V4h2l1 3zM4 0l3 3-2 1z" fill="var(--navy)"/></svg>Gardening</div>
  <div class="svc"><svg width="8" height="7" viewBox="0 0 8 7"><circle cx="5" cy="1.5" r="1.2" fill="var(--navy)"/><path d="M0 5q2-1 4 0t4 0v1q-2 1-4 0t-4 0z" fill="var(--navy)"/></svg>Swimming Pools</div>
  <div class="svc"><svg width="8" height="7" viewBox="0 0 8 7"><path d="M4 0l3.2 1.2v2C7.2 5 5.6 6.4 4 7 2.4 6.4.8 5 .8 3.2v-2z" fill="var(--navy)"/></svg>Security</div>
  <div class="svc"><svg width="8" height="7" viewBox="0 0 8 7"><rect x=".5" y="1.5" width="7" height="5" rx=".6" fill="none" stroke="var(--navy)" stroke-width=".9"/><path d="M2.5 0l1.5 1.5L5.5 0" stroke="var(--navy)" stroke-width=".6" fill="none"/></svg>TV Services</div>
  <div class="svc"><svg width="8" height="7" viewBox="0 0 8 7"><path d="M1 0h6L4.5 3v3h1.5v1H2V6h1.5V3z" fill="var(--navy)"/></svg>Pool Bar</div>
  <p style="margin-top:4px">Additionally, CDC are responsible on behalf of the Owners for keeping ALL the external aspects of the buildings painted, handrails upkeep, roofs and chimneys maintained and for ensuring an appropriate/adequate level of security is always maintained.</p>
</div></section>

<section class="page c4 r2"><div class="pad">
  <div class="sec" style="font-size:7.2px;padding:5px 8px;margin-bottom:10px;width:132px">Owners- Primary Obligations</div>
  <p>All Owners have equal OBLIGATIONS / COMMITMENT / RESPONSIBILITIES within our condominium complex.</p>
  <div class="mand">The following Owner Obligations are <b>MANDATORY:</b></div>
  <div class="item"><span class="n">1</span><p>To ensure the Property Management company (CDC) are made aware immediately of any improvements identified or required.</p></div>
  <div class="item"><span class="n">2</span><p>To always ensure ALL users of your apartment respect and adhere to the Rules and Regulations of the Condominium (refer to the separate Rules and Regulations document)</p></div>
  <div class="item"><span class="n">3</span><p>To recognise the Owners elected Board as our primary representatives in relation to the successful operational running and financial management of the complex during their term in office.</p></div>
  <div class="item"><span class="n">4</span><p>The areas outside each property boundary is communal, therefore Owners are reminded not to place / fix any obstruction within the communal areas.</p></div>
  <div class="item"><span class="n">5</span><p>To pay relevant Condominium Fees on time.</p></div>
  <div class="item"><span class="n">6</span><p>To pay any Late Payment Fees / Fines in a prompt timeframe.</p></div>
  <div class="item"><span class="n">7</span><p>To inform the local government financial authority that if a property is being used for commercial gain, through rental income or similar.</p></div>
  <div class="item"><span class="n">8</span><p>To be mindful of your fellow owners and neighbours and ensure noise levels and behaviour are in keeping with our Rules and Regulations.</p></div>
  <div class="item"><span class="n">9</span><p>To report to Security any / all suspicious incidents or behaviour unbecoming of the Rules of the Condominium.</p></div>
</div></section>

<section class="page c1 r3"><div class="pad" style="padding-top:16px">
  <div class="item"><span class="n">10</span><p>To report to Security any unruly behavior, at any time of the day but particularly after the 9pm threshold, that breaches our Peace and Tranquility rules.</p></div>
  <div class="item"><span class="n">11</span><p>To report to the Property Management Company of any external repairs required on your property.</p></div>
  <div class="item"><span class="n">12</span><p>To report to the Property Management Company anything that is broken or in need of repair within the Complex.</p></div>
  <div class="item"><span class="n">13</span><p>Ensure the Central Area Gardens are always kept tidy, by placing all waste in the waste receptacles provided throughout the Gardens area.</p></div>
  <div class="item"><span class="n">14</span><p>Ensure that all the "entrance doors" to the Gardens are closed after entry and NEVER left in the open position following either entry to or exit from the Gardens.</p></div>
  <div class="item"><span class="n">15</span><p>Dogs are not allowed in the Gardens at any time (on a lead or off), even if you own a ground floor Apartment.</p></div>
  <div class="item"><span class="n">16</span><p>Observing the rule that playing / practicing Golf is not allowed in the Gardens.</p></div>
  <div class="item"><span class="n">17</span><p>If children playing football, then Adults / Parents need to provide a reminder that footballs should not be aimed at flower beds / shrubbery or to be kicked repeatedly against the central Building housing the Bar.</p></div>
  <div class="item"><span class="n">18</span><p>Ensure that any "repairs / building work in your apartment" is not carried out during the period June – September.</p></div>
  <div class="item"><span class="n">19</span><p>Drones are not allowed to be used inside the Gardens Areas.</p></div>
  <div class="item"><span class="n">20</span><p>Ensure that Gas and Electric barbeques are the only types allowed.</p></div>
  <div class="item"><span class="n">21</span><p>Owners and their guests are fully responsible for their own safety and risks when using our swimming pools and hot tub – WE DO NOT HAVE LIFEGUARDS!</p></div>
</div></section>

<section class="page c2 r3"><div class="pad" style="padding-top:16px">
  <div class="item"><span class="n">22</span><p>NO DRINKS ARE ALLOWED in any pool or jacuzzi within the Gardens area.</p></div>
  <div class="item"><span class="n">23</span><p>Owners and their guests are not allowed to take glassware of any type into the Gardens area.</p></div>
  <div class="item"><span class="n">24</span><p>Owners and their guests are NOT ALLOWED to reserve sunbeds by placing towels or clothing or similar on them.</p></div>
  <div class="item"><span class="n">25</span><p>Sunbeds are for use at the Pool areas and NOT to be taken to individual apartments for use.</p></div>
  <div class="item"><span class="n">26</span><p>FINALLY, OWNERS MUST FAMILIARISE THEMSELVES AND THEIR GUESTS OF THEIR OBLIGATIONS, ADHERANCE TO OUR RULES AND REGULATIONS RELATED TO THE USE OF THE GARDENS AREA.</p></div>
</div></section>

<section class="page c3 r3"><div class="pad">
  <div class="sec" style="margin-bottom:5px">Valuable Information</div>
  <p>If you are a new Owner, or even existing Owner – there is so much information that would be of value to you, we have tried our best to summarise some of it within this section – but more than happy to receive updates on anything else Owners would like to add...</p>
  <div class="sec" style="margin-bottom:5px;width:82px">Your Apartment</div>
  <p>Each Owner is responsible for their own apartment's internal aspect and can furnish it to whatever standards they choose (but compliant with relevant buildings regulations obviously) , noting that any modernization / enhancements that involve excess noise cannot be carried out in the months June – September.</p>
  <p>Although many apartments have been modernised / updated / upgraded - each were originally provided with Gas supply, Electricity supply and a Fireplace. Some Owners have removed the fireplace, and some have also ceased using the Gas and rely only on Electricity.</p>
  <p>Ground floor apartments have an area within the Gardens area that is part of their "Fraction" just like others have with a Balcony. Upkeep / Repairs / Painting / of these areas within each "Fraction" is the responsibility of the appointed Property Management Company and is included within the annual fees that Owners pay. Should any owner require assistance in this regard then contact directly with the Property Management company is the route.</p>
  <p>Painting and general upkeep of the Condominium buildings in their entirety is the responsibility of the Property Management company and the cost of this is included within the Owners annual fees. So, for example an owner's apartment surrounding external walls and area will be painted on a scheduled cycle of upkeep.</p>
  <p>Weekly cleaning of the elevators / external flooring tiles / handrails and metalwork is carried out throughout the complex, the cost of which is covered by the Owners fees.</p>
</div></section>

<section class="page c4 r3"><div class="pad">
  <div class="sec" style="margin-bottom:6px">Our Rules and Regulations</div>
  <p>Over the years the Owners have agreed to keep standards in keeping with their vision, as such it's important that Owners are aware of these Standards to retain value of the complex. These Standards have evolved into "Rules and Regulations" and full details can be found within the SEPARATE Rules and Regulations document; however, a few Rules are included below</p>
  <div class="forbid">FORBIDDEN TO:</div>
  <div class="item"><span class="n">1</span><p>Perform on the fraction (apartment) any activity forbidden by law or offensive to good behaviour or perform any actions that impede or hinder the use of any other fractions or common areas</p></div>
  <div class="item"><span class="n">2</span><p>Hinder the tranquillity of the residential area with loud voices, music or sounds, noises, vibrations, heat, smoke, or any other similar occurrences</p></div>
  <div class="item"><span class="n">3</span><p>Place on the terraces, windows, and balconies any objects which are not duly protected from falling.</p></div>
  <div class="item"><span class="n">4</span><p>Throw out debris, cigarette buds or any other type of rubbish;</p></div>
  <div class="item"><span class="n">5</span><p>Keep animals in the Apartment other than dogs, cats, caged birds, or fish.</p></div>
  <div class="item"><span class="n">6</span><p>Dogs are not allowed in the central garden area under any circumstances</p></div>
  <div class="item"><span class="n">7</span><p>Dogs must be kept only on the walkways by the roads provided a leash and/or muzzle is used. They should be kept inside the Apartment at night (not on a balcony) and are not permitted in any common area except when passing through such a common area with their owner;</p></div>
  <div class="item"><span class="n">8</span><p>Use the space of the parking next to the building to do any work, washing, changing of oil or repairs to any private vehicles or not</p></div>
  <div class="item"><span class="n">9</span><p>Practise or play golf, in the central garden area</p></div>
</div></section>

<section class="page c1 r4"><div class="pad" style="padding-top:14px">
  <div class="item"><span class="n">10</span><p>Generally, practise or adopt any behaviour which might violate the conditions of the present rules and regulations as stipulated within the Rules and Regulations document</p></div>
  <div class="item"><span class="n">11</span><p>Use Electrical points to charge a vehicle in the B14 and B15 garages, unless it's a specified charging point owned by the car space Owner, the costs of which will require to be fully borne by the relevant owner;</p></div>
  <div class="item"><span class="n">12</span><p>Be particularly cautious with noise levels inside and outside your Apartment during the period between 23h00 and 8h00; be mindful that Security will be contacted and take necessary actions should they receive reports of excessive noise during these hours.</p></div>
  <p style="color:var(--blue);font-weight:700;font-size:4.6px;text-align:left">Additionally, we have produced a comprehensive set of Rules for the Gardens area, all Owners and their Guests must adhere to (displayed beside each swimming pool and DETAILED BELOW) relating to the use of the Common Gardens area, including:</p>
  <div class="item"><span class="n">1</span><p>Pools can only be used between the hours of 07.00am - 21.00pm;</p></div>
  <div class="item"><span class="n">2</span><p>Pool Sunbeds and umbrellas use are on a first come basis, <span style="color:var(--blue)">NO RESERVING OF THESE IS ALLOWED</span></p></div>
  <div class="item"><span class="n">3</span><p>Umbrellas cannot be relocated away from the swimming pools</p></div>
  <div class="item"><span class="n">4</span><p>The North pool (beside B14 and B15) has been designated as a swimming only pool. Inflatables and ball games are therefore not permitted at this pool at any time</p></div>
  <div class="item"><span class="n">5</span><p>Adhering to the "High Season Procedures" developed and agreed by the Owners and contained within Appendix 1 of this Owners Handbook</p></div>
  <div class="item"><span class="n">6</span><p>Don't climb up trees, the snack-bar awning, the changing rooms, or any other existing construction</p></div>
  <div class="item"><span class="n">7</span><p>Don't pick flowers, or dig up any of the plants within the Gardens area</p></div>
  <div class="item"><span class="n">8</span><p>Keep children (less than 12 years old) under constant supervision of an adult</p></div>
</div></section>

<section class="page c2 r4"><div class="pad" style="padding-top:14px">
  <div class="item"><span class="n">9</span><p>Personal CCTV or equivalent is not allowed to record in the Gardens or Common areas of the Condominium;</p></div>
  <div class="item"><span class="n">10</span><p>Drones of any sort are not allowed to be used in the Gardens Common area;</p></div>
  <div class="item"><span class="n">11</span><p>Ensure the locked gates to the Gardens area are properly and fully closed upon entry and exit, AT ALL TIMES, as this enhances the Gardens security;</p></div>
  <div class="item"><span class="n">12</span><p>Full details of our Gardens Rules and Regulations are contained within the RULES AND REGULATIONS DOCUMENT.</p></div>
  <div class="important">
    <svg width="20" height="20" viewBox="0 0 20 20"><rect x="2" y="2" width="17" height="17" rx="3" fill="#8e1b1b"/><rect x="0" y="0" width="17" height="17" rx="3" fill="var(--red)"/><rect x="7.3" y="3" width="2.4" height="7.5" rx="1" fill="#fff"/><circle cx="8.5" cy="13.3" r="1.4" fill="#fff"/></svg>
    <span>IMPORTANT NOTES:</span>
  </div>
  <div class="tick"><svg width="9" height="9" viewBox="0 0 9 9"><circle cx="4.5" cy="4.5" r="3.8" fill="none" stroke="var(--navy)" stroke-width=".9"/><path d="M2.5 4.6l1.5 1.5L8 1.5" stroke="var(--navy)" stroke-width="1" fill="none"/></svg><p>RFID access fobs to the 6 Gardens area locked gates have been issued to each apartment Owner.</p></div>
  <div class="tick"><svg width="9" height="9" viewBox="0 0 9 9"><circle cx="4.5" cy="4.5" r="3.8" fill="none" stroke="var(--navy)" stroke-width=".9"/><path d="M2.5 4.6l1.5 1.5L8 1.5" stroke="var(--navy)" stroke-width="1" fill="none"/></svg><p>If a fob is either lost or damaged, such that it no longer operates, CDC should be notified immediately whereupon they will 'de-register' the lost or damaged fob (such that the gate readers will no longer accept such a fob) and arrange for a replacement fob to be issued to the relevant owner (for a fee).</p></div>
  <div class="tick"><svg width="9" height="9" viewBox="0 0 9 9"><circle cx="4.5" cy="4.5" r="3.8" fill="none" stroke="var(--navy)" stroke-width=".9"/><path d="M2.5 4.6l1.5 1.5L8 1.5" stroke="var(--navy)" stroke-width="1" fill="none"/></svg><p>At all times apartment owners remain accountable for the use of every fob allocated to their apartment, regardless of who actually uses the fob.</p></div>
</div></section>

<section class="page c3 r4"><div class="pad">
  <div class="sec" style="margin-bottom:4px">TV and Internet Services</div>
  <h3><svg width="8" height="7" viewBox="0 0 8 7" style="vertical-align:-1px"><rect x=".5" y="1.5" width="7" height="5" rx=".6" fill="none" stroke="var(--navy)" stroke-width=".9"/><path d="M2.5 0l1.5 1.5L5.5 0" stroke="var(--navy)" stroke-width=".6" fill="none"/></svg> TV</h3>
  <p>Included within your annual Condominium Fees is access to many TV channels delivered through the co-axial tv cable points within your Apartment. Should you experience any difficulties accessing the TV channels please contact Security.</p>
  <h3><svg width="7" height="7" viewBox="0 0 7 7" style="vertical-align:-1px"><circle cx="3.5" cy="3.5" r="3" fill="none" stroke="var(--navy)" stroke-width=".8"/><ellipse cx="3.5" cy="3.5" rx="1.3" ry="3" fill="none" stroke="var(--navy)" stroke-width=".6"/><path d="M.5 3.5h6" stroke="var(--navy)" stroke-width=".6"/></svg> INTERNET</h3>
  <p>Owners are free to use any of the many Internet service providers in Portugal, however your Board have negotiated a very good arrangement with a local renowned Internet provider called NetBreeze.</p>
  <p>NetBreeze, as well as providing Internet services directly to the Owners, they also have a contract with the Property Management company to maintain the co-axial TV services mentioned above. NetBreeze details can be found at <span style="color:var(--blue)">https://www.netbreeze.example</span></p>
  <div class="sec sm" style="margin:4px 0 6px">Harbour Living Company (Customer Services)</div>
  <p>Customer Services for the Monte Azul resort is provided by Harbour Living. All post to your Apartment is delivered to Customer Services and not the boxes outside your Apartment.</p>
  <p>Based within the office complex next to Anchor pub, is the Harbour Living (HL) company. Marta is the Manager at HL and she is assisted by Ines in the office. Full details can be found at https://www.harbourliving.example</p>
  <p>Harbour Living provide a range of services to Owners including receiving mail, parcel deliveries, maintaining and cleaning properties and work with some of the Owners who rent out their property through HL.</p>
  <p>Harbour Living also provide property management services to individual owner.</p>
</div></section>

<section class="page c4 r4"><div class="pad">
  <div class="sec sm" style="margin-bottom:6px">Restaurants – Cafes – Shops:</div>
  <div class="biz"><span class="name"><svg width="6" height="6" viewBox="0 0 9 9"><circle cx="4.5" cy="4.5" r="3.8" fill="none" stroke="var(--navy)" stroke-width="1"/><path d="M2.5 4.6l1.5 1.5L8 1.5" stroke="var(--navy)" stroke-width="1.1" fill="none"/></svg>Anchor Pub</span><span class="tel"><svg width="4" height="5" viewBox="0 0 4 5"><path d="M1 0h1v1.4H1.3c-.1 1 .2 1.6.8 2.2H3V5H2C.5 4 0 2.6 0 1.4 0 .6.4 0 1 0z" fill="var(--navy)"/></svg>+351 920 000 201</span></div>
  <div class="biz"><span class="name"><svg width="6" height="6" viewBox="0 0 9 9"><circle cx="4.5" cy="4.5" r="3.8" fill="none" stroke="var(--navy)" stroke-width="1"/><path d="M2.5 4.6l1.5 1.5L8 1.5" stroke="var(--navy)" stroke-width="1.1" fill="none"/></svg>Cork Bistro</span><span class="tel"><svg width="4" height="5" viewBox="0 0 4 5"><path d="M1 0h1v1.4H1.3c-.1 1 .2 1.6.8 2.2H3V5H2C.5 4 0 2.6 0 1.4 0 .6.4 0 1 0z" fill="var(--navy)"/></svg>+351 960 000 202</span></div>
  <div class="biz" style="margin-bottom:8px"><span class="name"><svg width="6" height="6" viewBox="0 0 9 9"><circle cx="4.5" cy="4.5" r="3.8" fill="none" stroke="var(--navy)" stroke-width="1"/><path d="M2.5 4.6l1.5 1.5L8 1.5" stroke="var(--navy)" stroke-width="1.1" fill="none"/></svg>Ember Grill</span><span class="tel"><svg width="4" height="5" viewBox="0 0 4 5"><path d="M1 0h1v1.4H1.3c-.1 1 .2 1.6.8 2.2H3V5H2C.5 4 0 2.6 0 1.4 0 .6.4 0 1 0z" fill="var(--navy)"/></svg>+351 289 000 203</span></div>
  <div class="sec sm" style="margin-bottom:6px">Café's with in the resort:</div>
  <div class="biz"><span class="name"><svg width="6" height="6" viewBox="0 0 9 9"><circle cx="4.5" cy="4.5" r="3.8" fill="none" stroke="var(--navy)" stroke-width="1"/><path d="M2.5 4.6l1.5 1.5L8 1.5" stroke="var(--navy)" stroke-width="1.1" fill="none"/></svg>Monte Azul Café</span><span class="tel"><svg width="4" height="5" viewBox="0 0 4 5"><path d="M1 0h1v1.4H1.3c-.1 1 .2 1.6.8 2.2H3V5H2C.5 4 0 2.6 0 1.4 0 .6.4 0 1 0z" fill="var(--navy)"/></svg>+351 960 000 204</span></div>
  <div class="biz" style="margin-bottom:8px"><span class="name"><svg width="6" height="6" viewBox="0 0 9 9"><circle cx="4.5" cy="4.5" r="3.8" fill="none" stroke="var(--navy)" stroke-width="1"/><path d="M2.5 4.6l1.5 1.5L8 1.5" stroke="var(--navy)" stroke-width="1.1" fill="none"/></svg>Café da Praça</span><span class="tel"><svg width="4" height="5" viewBox="0 0 4 5"><path d="M1 0h1v1.4H1.3c-.1 1 .2 1.6.8 2.2H3V5H2C.5 4 0 2.6 0 1.4 0 .6.4 0 1 0z" fill="var(--navy)"/></svg>+351 960 000 205</span></div>
  <div class="sec sm" style="margin-bottom:6px">Supermarket:</div>
  <p class="hint">We have a small supermarket Mini Mercado Sol within the resort (next to the Monte Azul</p>
  <div class="sec sm" style="margin:4px 0 6px">Hairdressers within the complex:</div>
  <div class="biz"><span class="name" style="flex-basis:85px"><svg width="6" height="6" viewBox="0 0 9 9"><circle cx="4.5" cy="4.5" r="3.8" fill="none" stroke="var(--navy)" stroke-width="1"/><path d="M2.5 4.6l1.5 1.5L8 1.5" stroke="var(--navy)" stroke-width="1.1" fill="none"/></svg>Hair and BeautySalon</span><span class="tel"><svg width="4" height="5" viewBox="0 0 4 5"><path d="M1 0h1v1.4H1.3c-.1 1 .2 1.6.8 2.2H3V5H2C.5 4 0 2.6 0 1.4 0 .6.4 0 1 0z" fill="var(--navy)"/></svg>+351 920 000 206</span></div>
  <div class="biz"><span class="name" style="flex-basis:85px"><svg width="6" height="6" viewBox="0 0 9 9"><circle cx="4.5" cy="4.5" r="3.8" fill="none" stroke="var(--navy)" stroke-width="1"/><path d="M2.5 4.6l1.5 1.5L8 1.5" stroke="var(--navy)" stroke-width="1.1" fill="none"/></svg>Salon Amélie</span><span class="tel"><svg width="4" height="5" viewBox="0 0 4 5"><path d="M1 0h1v1.4H1.3c-.1 1 .2 1.6.8 2.2H3V5H2C.5 4 0 2.6 0 1.4 0 .6.4 0 1 0z" fill="var(--navy)"/></svg>+351 920 000 207</span></div>
</div></section>

</body>
</html>
```